Business Card for a Dental Office

The design should communicate integrity, quality and reliability. We also want the card look elegant, simple, but still stand out, different from the traditional-dental-office business card.

Industry/Entity Type

Business

```html
<!DOCTYPE html>
<html lang="en">
<head>
<meta charset="utf-8">
<title>Halden Dental Studio – Business Card</title>
<link href="https://fonts.googleapis.com/css2?family=Jost:wght@300;500&display=swap" rel="stylesheet">
<style>
  :root {
    --backdrop: #d9d4cf;
    --card: #ffffff;
    --ink: #2b2a2c;
    --yellow: #f1ec48;
    --text: #1e1e1e;
  }
  * { margin: 0; padding: 0; box-sizing: border-box; }
  html, body {
    width: 1200px; height: 800px; overflow: hidden;
    background: var(--backdrop);
    font-family: "Jost", "Futura", sans-serif;
  }
  .card {
    position: absolute; left: 75px; top: 100px;
    width: 1050px; height: 600px;
    background: var(--card);
    overflow: hidden;
    box-shadow: 0 6px 18px rgba(0,0,0,0.12);
  }
  .corner-block {
    position: absolute; left: 0; top: 0;
    width: 250px; height: 150px; background: var(--ink);
  }
  .corner-rule {
    position: absolute; left: 250px; top: 0;
    width: 16px; height: 150px; background: var(--yellow);
  }
  .brand {
    position: absolute; left: 330px; top: 0; height: 150px;
    display: flex; align-items: center; gap: 20px;
  }
  .brand-mark {
    width: 64px; height: 64px; background: var(--ink);
  }
  .brand-name {
    font-weight: 500; font-size: 44px; color: var(--ink);
    letter-spacing: 1px; text-transform: uppercase; line-height: 1;
  }
  .name-band {
    position: absolute; left: 0; top: 150px;
    width: 100%; height: 115px; background: var(--yellow);
    display: flex; align-items: center; padding-left: 150px;
  }
  .name-band .person {
    font-weight: 300; font-size: 54px; color: var(--text); letter-spacing: 0.5px;
  }
  .icon-column {
    position: absolute; left: 0; top: 265px;
    width: 120px; height: 250px; background: var(--ink);
    display: flex; flex-direction: column; align-items: center; justify-content: space-evenly;
  }
  .icon-column svg { width: 40px; height: 40px; }
  .icon-rule {
    position: absolute; left: 120px; top: 265px;
    width: 16px; height: 335px; background: var(--yellow);
  }
  .icon-base {
    position: absolute; left: 0; top: 515px;
    width: 136px; height: 16px; background: var(--yellow);
  }
  .contacts {
    position: absolute; left: 180px; top: 285px;
    display: flex; flex-direction: column; justify-content: space-around;
    height: 220px;
    font-weight: 300; font-size: 44px; color: var(--text);
    white-space: nowrap;
  }
</style>
</head>
<body>
  <div class="card">
    <div class="corner-block"></div>
    <div class="corner-rule"></div>

    <div class="brand">
      <div class="brand-mark"></div>
      <span class="brand-name">Halden Dental Studio</span>
    </div>

    <div class="name-band">
      <span class="person">Mara Lindqvist, Dentist</span>
    </div>

    <div class="icon-column">
      <svg viewBox="0 0 24 24" aria-label="Phone">
        <path fill="#fff" d="M6.6 10.8c1.4 2.8 3.8 5.1 6.6 6.6l2.2-2.2c.3-.3.7-.4 1-.2 1.1.4 2.3.6 3.6.6.6 0 1 .4 1 1V20c0 .6-.4 1-1 1C10.6 21 3 13.4 3 4c0-.6.4-1 1-1h3.5c.6 0 1 .4 1 1 0 1.3.2 2.5.6 3.6.1.3 0 .7-.2 1z"/>
      </svg>
      <svg viewBox="0 0 24 24" aria-label="Email">
        <rect x="2" y="5" width="20" height="14" fill="#fff"/>
        <path d="M2 5l10 8 10-8" fill="none" stroke="#2b2a2c" stroke-width="1.5"/>
      </svg>
      <svg viewBox="0 0 24 24" aria-label="Website">
        <rect x="4" y="5" width="16" height="11" fill="none" stroke="#fff" stroke-width="1.8"/>
        <path d="M2 19h20" stroke="#fff" stroke-width="2"/>
      </svg>
    </div>
    <div class="icon-rule"></div>
    <div class="icon-base"></div>

    <div class="contacts">
      <span class="phone">555-218-4630</span>
      <span class="email">mara@haldendentalstudio.com</span>
      <span class="web">www.haldendentalstudio.com</span>
    </div>
  </div>
</body>
</html>
```